Luxury Wine Label for New Startup Winery

We need a wine label for our new winery startup. We have worked with a local designer but do not feel the resulting label / logo have the elevation required to present our brand as a luxury wine. Our winery is called "Quailbrook Vineyards" and we are focused on extremely high quality hand crafted artisan and estate wines from the Pacific Northwest.
We would like to see designs that utilize a tree line, or other imagery that represents the "Quailbrook" part of our company name. Another interesting feature could be wood grain.
A logo will be required based on your design so please design with this in mind:
This logo should be consistent with the wine bottle label design, and should be representative of our high end exclusive wine while giving a sense of place (Oregon/ Pacific Northwest.)
I will supply an image of the design we received from our local designer, PLEASE NOTE: in general we do like wood grain and tree line concepts but feel the execution was poorly done.
ATTN: Logo design should be suitable for use on: Bottles (Red wine/rose/white wine), Bussiness cards, vehicle signage, business signage, etc
P.S.:
If you have a design that is not outside the box we are still interested in seeing it.
Label is for a burgundy style bottle with a label height of 3.5 - 4" and a width of 3.5-4"
any label <= 4"x4" and >=3.5"x3.5" will be acceptable:
HOWEVER Width should be greater than or equal to height due to the bottle format
Target Market(s)
Wine enthusiasts with adequate discretionary budgets to afford $100 bottles of wine.
Industry/Entity Type
Wine / Winery
Requirements
Must have
- A sense of luxury, a feel of exclusivity, and a theme consistent with our product and brand name
Nice to have
- Tree line, wood grain or other wood themes. Serif fonts
Should not have
- anything cheesy, off topic, hard to read script fonts or anything that makes the label hard to read from a few feet away or too busy

```html
<!DOCTYPE html>
<html lang="en">
<head>
<meta charset="utf-8">
<title>Quailbrook Vineyards – Red Wine Label</title>
<link rel="stylesheet" href="https://fonts.googleapis.com/css2?family=Cormorant+Garamond:wght@500&family=Pinyon+Script&display=swap">
<style>
  :root {
    --page: #ffffff;
    --gold: #e2b23a;
    --gold-light: #f4cf55;
    --gold-rule: #e8cf9a;
    --wood-dark: #2a0d14;
    --wood-mid: #4a2029;
    --wood-light: #5c2c35;
    --panel: #d8ced3;
    --panel-light: #e4dde1;
    --ink: #3a0f18;
  }
  html, body {
    margin: 0;
    width: 1200px;
    height: 1200px;
    overflow: hidden;
    background: var(--page);
  }
  .label {
    position: absolute;
    left: 104px;
    top: 104px;
    width: 992px;
    height: 992px;
    box-sizing: border-box;
    border: 1.5px solid var(--gold-rule);
    border-radius: 20px;
    background: var(--page);
  }
  .wood-field {
    position: absolute;
    left: 24px;
    top: 24px;
    width: 944px;
    height: 944px;
    background:
      radial-gradient(ellipse at 30% 20%, var(--wood-light) 0%, transparent 55%),
      radial-gradient(ellipse at 75% 80%, var(--wood-light) 0%, transparent 50%),
      linear-gradient(135deg, var(--wood-mid) 0%, var(--wood-dark) 100%);
  }
  .name-panel {
    position: absolute;
    left: 184px;
    top: 305px;
    width: 624px;
    height: 354px;
    background: linear-gradient(160deg, var(--panel-light) 0%, var(--panel) 60%, var(--panel-light) 100%);
  }
  .gold-rule {
    position: absolute;
    left: 0;
    right: 0;
    top: 10px;
    height: 4px;
    background: linear-gradient(90deg, var(--gold) 0%, var(--gold-light) 50%, var(--gold) 100%);
  }
  .seal {
    position: absolute;
    left: 264px;
    top: -50px;
    width: 96px;
    height: 96px;
    box-sizing: border-box;
    border-radius: 50%;
    border: 6px solid var(--gold);
    background: var(--wood-dark);
  }
  .winery-name {
    position: absolute;
    left: 0;
    right: 0;
    top: 68px;
    margin: 0;
    text-align: center;
    font-family: "Cormorant Garamond", Georgia, serif;
    font-weight: 500;
    font-size: 68px;
    line-height: 92px;
    letter-spacing: 0.1em;
    text-transform: uppercase;
    color: var(--ink);
  }
  .winery-name span { display: block; }
  .wine-type {
    position: absolute;
    left: 0;
    right: 0;
    top: 268px;
    margin: 0;
    text-align: center;
    font-family: "Pinyon Script", cursive;
    font-size: 40px;
    color: var(--ink);
  }
</style>
</head>
<body>
  <div class="label">
    <div class="wood-field" role="img" aria-label="Dark burgundy swirling wood grain texture"></div>
    <div class="name-panel">
      <div class="gold-rule"></div>
      <div class="seal"></div>
      <h1 class="winery-name"><span>Quailbrook</span><span>Vineyards</span></h1>
      <p class="wine-type">Red Wine</p>
    </div>
  </div>
</body>
</html>
```